We need a business card for our gym. We are a PowerCore affiliate in Decatur Georgie established 2008. Our company name is Rally Functional Fitness. PowerCore Building Prime Fitness. Instagram and website is @rallygym. Hashtags we use #rallywithheart #madetorally We want something similar to the the black and neon green design attached but a different color scheme. No neon colors. Are company colors are the same as the blue and white card attached. We are open to ideas as far as colors however - just no neon.

Contact Information for Business Card

Rally Functional Fitness
472 Halvern Drive
Decatur GA 30041
Phone 404.555.0187 Website www.rallygym.example

Font styles to use
Other font styles liked:
• Futura Extra Bold Condensed

Colors

Designer to choose colors to be used in the design.

Requirements
Must have
• Our primary font we typically use for our name is Futura Extra Bold Condensed
Nice to have
• I attached a card from that is black and neon green from Zorva that we would like something similar. The blue and white is more similar to our colors. We also use have used black and white in the past. We use the chevrons as out logo. We are a PowerCore affiliate so I included a logo from them as well that may or may not be used on the card. Our instagram is @rallygym hashtags #madetorally #rallywithheart
Should not have
• No neon colors

```html
<!DOCTYPE html>
<html lang="en">
<head>
<meta charset="utf-8">
<title>Rally Functional Fitness – Business Card</title>
<link rel="stylesheet" href="https://fonts.googleapis.com/css2?family=Oswald:wght@400;700&family=Montserrat:wght@400;500&display=swap">
<style>
  :root {
    --page-bg: #2a2a2c;
    --card-white: #ffffff;
    --card-dark: #1c1d1f;
    --card-dark-2: #26272a;
    --brand-blue: #35b6e8;
    --ink: #1a1a1a;
    --rule: #8a8a8a;
  }
  * { margin: 0; padding: 0; box-sizing: border-box; }
  html, body { width: 1200px; height: 1108px; overflow: hidden; }
  body {
    background: var(--page-bg);
    display: flex;
    align-items: center;
    justify-content: center;
    gap: 60px;
  }
  .card {
    width: 434px;
    height: 760px;
    border-radius: 30px;
    overflow: hidden;
    position: relative;
  }
  .card-front {
    background: var(--card-white);
    color: var(--ink);
    text-align: center;
    font-family: "Montserrat", sans-serif;
  }
  .brand-name {
    position: absolute;
    top: 96px;
    left: 0; right: 0;
    font-family: "Oswald", sans-serif;
    font-weight: 700;
    color: var(--brand-blue);
    text-transform: uppercase;
    line-height: 1.05;
  }
  .brand-name .line-main { display: block; font-size: 64px; letter-spacing: 1px; }
  .brand-name .line-sub { display: block; font-size: 24px; letter-spacing: 2px; }
  .contact-block {
    position: absolute;
    top: 370px;
    left: 70px; right: 70px;
  }
  .person-name {
    font-family: "Oswald", sans-serif;
    font-weight: 400;
    font-size: 36px;
    color: var(--brand-blue);
    text-transform: uppercase;
    line-height: 1.1;
  }
  .person-role {
    font-size: 17px;
    text-transform: uppercase;
    letter-spacing: 1px;
    margin-top: 2px;
  }
  .icon-divider {
    display: flex;
    align-items: center;
    gap: 6px;
    margin: 14px 0 16px;
  }
  .icon-divider .rule { flex: 1; height: 1px; background: var(--rule); }
  .icon-divider svg { width: 22px; height: 22px; }
  .contact-lines { font-size: 18px; line-height: 1.3; }
  .plain-rule { height: 1px; background: var(--rule); margin: 18px 0 14px; }
  .address { font-size: 16px; line-height: 1.3; }

  .card-back {
    background: var(--card-dark);
  }
  .back-pattern {
    position: absolute;
    inset: 0;
    background: linear-gradient(160deg, var(--card-dark-2), var(--card-dark));
  }
  .back-mark {
    position: absolute;
    right: 50px;
    bottom: 230px;
    font-family: "Oswald", sans-serif;
    font-weight: 700;
    font-size: 34px;
    color: var(--brand-blue);
    text-transform: uppercase;
    letter-spacing: 1px;
  }
</style>
</head>
<body>
  <section class="card card-front">
    <h1 class="brand-name">
      <span class="line-main">Rally</span>
      <span class="line-sub">Functional Fitness</span>
    </h1>
    <div class="contact-block">
      <h2 class="person-name">Marcus Ellery</h2>
      <p class="person-role">Expert Coaches</p>
      <div class="icon-divider">
        <span class="rule"></span>
        <svg viewBox="0 0 22 22" aria-label="Phone">
          <circle cx="11" cy="11" r="11" fill="var(--brand-blue)"/>
          <path d="M7.5 6.5l2 0 1 2.5-1.2 1a6 6 0 0 0 2.7 2.7l1-1.2 2.5 1 0 2c0 .6-.5 1-1 1A8.5 8.5 0 0 1 6.5 7.5c0-.5.4-1 1-1z" fill="#fff"/>
        </svg>
        <svg viewBox="0 0 22 22" aria-label="Email">
          <circle cx="11" cy="11" r="11" fill="var(--brand-blue)"/>
          <rect x="5.5" y="7.5" width="11" height="7.5" fill="none" stroke="#fff" stroke-width="1.3"/>
          <path d="M5.5 7.5l5.5 4 5.5-4" fill="none" stroke="#fff" stroke-width="1.3"/>
        </svg>
        <svg viewBox="0 0 22 22" aria-label="Website">
          <circle cx="11" cy="11" r="11" fill="var(--brand-blue)"/>
          <circle cx="11" cy="11" r="5.5" fill="none" stroke="#fff" stroke-width="1.3"/>
          <ellipse cx="11" cy="11" rx="2.4" ry="5.5" fill="none" stroke="#fff" stroke-width="1.1"/>
          <path d="M5.5 11h11" stroke="#fff" stroke-width="1.1"/>
        </svg>
        <span class="rule"></span>
      </div>
      <p class="contact-lines">
        404.555.0187<br>
        info@rallygym.example<br>
        www.rallygym.example
      </p>
      <div class="plain-rule"></div>
      <p class="address">
        472 Halvern Drive<br>
        Decatur GA 30041
      </p>
    </div>
  </section>

  <section class="card card-back">
    <div class="back-pattern" role="img" aria-label="Tonal dark chevron pattern covering the card back"></div>
    <p class="back-mark">Rally</p>
  </section>
</body>
</html>
```